Logo and Card design for KRV Home Solutions LLC

I need an edgier logo and business card designs. Current logo attached. I like the colors below. I would like the logo to incorporate a home in the design.
Title = Principal-Acquisitions
Email:KRVHOMESOLUTIONS@fernmail.example
555-214-0937
facebook
IG
2 sided business card with the front being contact info a slogan about selling a home fast. The back incorporating What we do. Buy houses, land, or commercial property as is. We find solutions to make the process of selling simple and fair.

Target Market(s)

Motivated house sellers.

Industry/Entity Type

Business

Contact Information for Business Card

Who we are: We are a Faith based Real Estate Investment Company. We pay cash for homes in any condition and can close quick. Whatever the reason you need to sell fast, we can help. We believe in creating win-win solutions to help you in your time of need. We care! We can help!

Logo Text

KRV Home Solutions LLC

Font styles to use
Sans Serif

Colors
33a6d7
0355a3
85abd2
cee9f5
9d9d9d
b2b2b2
ffffff

Requirements
Must have
• Old logo attached. I want something edgier.
• Company name, phone number, description on the back of what we can do. Pay all cash. Buy in as is condition. No fees,Commisions or closing costs.Close quick. No hassles with solutions to meet your unique situation.
• Call today for an offer within 24 hours.

```html
<!DOCTYPE html>
<html lang="en">
<head>
<meta charset="utf-8">
<title>KRV Home Solutions – Business Cards</title>
<link href="https://fonts.googleapis.com/css2?family=Roboto:wght@400;500;700&family=Roboto+Condensed:wght@400;700&display=swap" rel="stylesheet">
<style>
  :root {
    --navy: #1f3a7d;
    --navy-deep: #17306b;
    --grey: #9d9d9d;
    --grey-light: #b2b2b2;
    --ice: #eef3f6;
    --white: #ffffff;
    --page: #e9e7e3;
  }
  * { box-sizing: border-box; margin: 0; padding: 0; }
  html, body { width: 1200px; height: 886px; overflow: hidden; }
  body {
    background: var(--page);
    font-family: "Roboto", Arial, sans-serif;
    display: flex; align-items: center; justify-content: center; gap: 40px;
  }
  .card {
    position: relative; width: 540px; height: 309px; overflow: hidden;
    box-shadow: 0 6px 18px rgba(0,0,0,.18);
  }
  .card-front { background: var(--navy); color: var(--white); }
  .front-art { position: absolute; inset: 0; }
  .brand {
    position: absolute; display: flex; align-items: center; gap: 10px;
    white-space: nowrap; line-height: 1.1;
    font-family: "Roboto Condensed", Arial, sans-serif; font-weight: 700;
    letter-spacing: .5px; text-transform: uppercase;
  }
  .brand-mark { width: 20px; height: 20px; background: currentColor; flex: none; }
  .card-front .brand { top: 62px; left: 50%; transform: translateX(-50%); color: var(--navy); font-size: 30px; }
  .contact { position: absolute; left: 30px; top: 196px; }
  .contact .name { font-weight: 700; font-size: 17px; letter-spacing: .5px; text-transform: uppercase; }
  .contact .title, .contact .line { font-size: 11px; margin-top: 4px; text-transform: uppercase; white-space: nowrap; }
  .contact .line { display: flex; align-items: center; gap: 6px; }
  .contact svg { width: 10px; height: 10px; fill: var(--white); }
  .offer { position: absolute; left: 300px; top: 196px; width: 220px; list-style: none; font-size: 10.5px; line-height: 1.45; }
  .offer li { position: relative; padding-left: 10px; }
  .offer li::before { content: ""; position: absolute; left: 0; top: 6px; width: 4px; height: 4px; border-radius: 50%; background: var(--white); }

  .card-back { background: linear-gradient(160deg, var(--navy) 0%, var(--navy-deep) 100%); color: var(--white); text-align: center; }
  .card-back .brand { top: 38px; left: 50%; transform: translateX(-50%); font-size: 30px; color: var(--white); }
  .section-title { position: absolute; top: 96px; width: 100%; font-weight: 700; font-size: 13px; letter-spacing: 1px; }
  .about { position: absolute; top: 126px; left: 40px; right: 40px; font-size: 11.5px; line-height: 1.5; }
  .about p + p { margin-top: 10px; }
</style>
</head>
<body>
  <section class="card card-front">
    <svg class="front-art" viewBox="0 0 540 309" preserveAspectRatio="none">
      <defs>
        <linearGradient id="fade" x1="0" y1="0" x2="0" y2="1">
          <stop offset="0" stop-color="#ffffff" stop-opacity=".9"/>
          <stop offset="1" stop-color="#eef3f6" stop-opacity=".6"/>
        </linearGradient>
      </defs>
      <polygon points="0,0 540,0 540,120 290,178 0,120" fill="#c9cfc6" role="img" aria-label="Photograph of a suburban house with lawn, softly faded"/>
      <polygon points="0,0 540,0 540,120 290,178 0,120" fill="url(#fade)"/>
      <polyline points="0,124 290,182 540,124" fill="none" stroke="#ffffff" stroke-width="4"/>
      <polyline points="0,132 290,190 540,132" fill="none" stroke="#9d9d9d" stroke-width="6"/>
      <polyline points="0,140 290,198 540,140" fill="none" stroke="#b2b2b2" stroke-width="2"/>
    </svg>
    <div class="brand"><span class="brand-mark"></span>KRV Home Solutions</div>
    <div class="contact">
      <div class="name">Alex Marlow</div>
      <div class="title">Principal-Acquisitions</div>
      <div class="line">KRVHOMESOLUTIONS@fernmail.example</div>
      <div class="line"><svg viewBox="0 0 24 24"><path d="M6.6 10.8a15 15 0 0 0 6.6 6.6l2.2-2.2c.3-.3.7-.4 1-.2 1.1.4 2.3.6 3.6.6.6 0 1 .4 1 1V20c0 .6-.4 1-1 1A17 17 0 0 1 3 4c0-.6.4-1 1-1h3.5c.6 0 1 .4 1 1 0 1.3.2 2.5.6 3.6.1.3 0 .7-.2 1z"/></svg>555-214-0937</div>
      <div class="line"><svg viewBox="0 0 24 24"><circle cx="12" cy="12" r="10"/></svg>KRVHOMESOLUTIONS.example</div>
    </div>
    <ul class="offer">
      <li>Pay all cash. Buy in as is condition</li>
      <li>No fees,Commisions or closing costs</li>
      <li>Close quick. No hassles with solutions to meet your unique situation</li>
      <li>Call today for an offer within 24 hours</li>
    </ul>
  </section>

  <section class="card card-back">
    <div class="brand"><span class="brand-mark"></span>KRV Home Solutions</div>
    <h2 class="section-title">WHO WE ARE</h2>
    <div class="about">
      <p>We are a Faith based Real Estate Investment Company. We pay cash for homes in any condition and can close quick. Whatever the reason you need to sell fast, we can help. We believe in creating win-win solutions to help you in your time of need.</p>
      <p>Buy houses, land, or commercial property as is.<br>We find solutions to make the process of selling simple and fair.</p>
    </div>
  </section>
</body>
</html>
```